Business IT Services Billboard to attract local small businesses

We are Brivoqua, a premier Managed Service Provider (MSP) specializing in comprehensive IT services and VOIP phone solutions exclusively for businesses. Our goal is to create a dynamic and visually engaging billboard advertisement that not only highlights our cutting-edge IT solutions but also emphasizes our state-of-the-art VOIP phone services. This billboard should communicate our commitment to providing innovative, reliable, and holistic technology solutions.
See the attached supporting documentation.
Target Market(s)
small business
Industry/Entity Type
Information Technology
Colors
Designer to choose colors to be used in the design.
Look and feel
Each slider illustrates characteristics of the customer's brand and the style your logo design should communicate.

```html
<!DOCTYPE html>
<html lang="en">
<head>
<meta charset="utf-8">
<title>Brivoqua Billboard</title>
<link href="https://fonts.googleapis.com/css2?family=Montserrat:wght@500;600;700;800&display=swap" rel="stylesheet">
<style>
  :root {
    --page-bg: #e3e9f1;
    --navy-deep: #050d1e;
    --navy: #0b2147;
    --navy-mid: #123a6e;
    --accent-blue: #1e90f0;
    --bar-blue: #2b98ef;
    --white: #ffffff;
    --violet: #6a3fb8;
    --cyan-glow: #2fc4e6;
  }
  * { margin: 0; padding: 0; box-sizing: border-box; }
  html, body {
    width: 1157px;
    height: 1200px;
    overflow: hidden;
    background: var(--page-bg);
    font-family: "Montserrat", sans-serif;
  }
  .billboard {
    position: absolute;
    left: 30px;
    top: 440px;
    width: 1097px;
    height: 320px;
    overflow: hidden;
    background:
      radial-gradient(ellipse 60% 90% at 30% 10%, rgba(30, 80, 150, 0.45), transparent 70%),
      linear-gradient(100deg, var(--navy) 0%, var(--navy-deep) 55%, var(--navy-deep) 100%);
    box-shadow: 0 18px 30px rgba(20, 30, 50, 0.25);
  }
  .tech-illustration {
    position: absolute;
    left: 520px;
    top: 0;
    width: 577px;
    height: 250px;
    background:
      radial-gradient(circle at 65% 48%, rgba(106, 63, 184, 0.75) 0%, rgba(60, 40, 140, 0.45) 18%, transparent 40%),
      radial-gradient(circle at 12% 60%, rgba(47, 196, 230, 0.35) 0%, transparent 16%),
      radial-gradient(ellipse 70% 80% at 65% 50%, rgba(25, 90, 170, 0.45), transparent 75%);
  }
  .headline {
    position: absolute;
    left: 36px;
    top: 20px;
    font-weight: 800;
    font-size: 36.5px;
    line-height: 39.5px;
    color: var(--white);
    text-transform: uppercase;
    letter-spacing: -0.2px;
  }
  .headline .highlight, .subhead .highlight { color: var(--accent-blue); }
  .subhead {
    position: absolute;
    left: 36px;
    top: 150px;
    font-weight: 500;
    font-size: 23.5px;
    line-height: 31.5px;
    color: var(--white);
  }
  .cta-bar {
    position: absolute;
    left: 0;
    top: 235px;
    width: 591px;
    height: 61px;
    background: var(--bar-blue);
    border-radius: 0 22px 22px 0;
    display: flex;
    align-items: center;
  }
  .cta-lead {
    margin-left: 36px;
    font-weight: 500;
    font-size: 18.5px;
    line-height: 24px;
    color: var(--white);
  }
  .cta-divider {
    width: 1.5px;
    height: 40px;
    background: var(--white);
    margin: 0 16px 0 16px;
  }
  .cta-url {
    font-weight: 600;
    font-size: 32px;
    color: var(--white);
    letter-spacing: 0.2px;
  }
  .brand-name {
    position: absolute;
    right: 39px;
    top: 238px;
    font-weight: 800;
    font-size: 55px;
    line-height: 60px;
    color: var(--white);
    letter-spacing: 1px;
    text-transform: uppercase;
  }
</style>
</head>
<body>
  <section class="billboard">
    <div class="tech-illustration" role="img" aria-label="Glowing isometric illustration of a globe on a laptop surrounded by tablets, phones and connected network devices"></div>

    <h1 class="headline">
      Seamless <span class="highlight">Technology</span><br>
      Solutions for Modern<br>
      Businesses
    </h1>

    <p class="subhead">
      <span class="highlight">Innovative</span> IT and VOIP Solutions<br>
      Tailored for Your <span class="highlight">Business Success</span>
    </p>

    <div class="cta-bar">
      <p class="cta-lead">Transform Your<br>Tech Today At</p>
      <span class="cta-divider"></span>
      <p class="cta-url">www.brivoqua.com</p>
    </div>

    <p class="brand-name">Brivoqua</p>
  </section>
</body>
</html>
```